CBD AgriBusiness Verdant Trophy Business Card

We are HiTec producer of medical cannabis CBD Switzerland of high quality. Our website is alpinleaf.net, we will also revisit it graphically, the winner of this contest will be the graphic designer chosen for the new design of the website. We stand out by the skill of the team, many of our engineers we win cup cannabis. I join the current map to take as an example but to revisit completely: deletion of surname and first name, modification of funds (front / back), reorganization of text info, highlighting the address of the website. three characteristics define the business card: Professional, Class, refined. The business card must be optimized for soft-touch and selective varnish printing.

Target Market(s)

Customers and Suppliers

Industry/Entity Type

Agribusiness

Contact Information for Business Card

Logo, Tél / Whatsapp, mail, url du site : alpinleaf.net

Font styles to use
Sans Serif

Requirements
Must have
• Logo of alpinleaf.net
Nice to have
• a design that stands out well on the selective varnish
Should not have
• Last name and first name

```html
<!DOCTYPE html>
<html lang="en">
<head>
<meta charset="UTF-8">
<title>alpinleaf business card</title>
<link href="https://fonts.googleapis.com/css2?family=Lato:wght@400;900&display=swap" rel="stylesheet">
<style>
  :root {
    --leaf-green: #9cc96b;
    --paper-white: #ffffff;
    --ink-grey: #3a3a3a;
    --backdrop: #e4e4e4;
    --card-shadow: rgba(0, 0, 0, 0.18);
  }
  * { margin: 0; padding: 0; box-sizing: border-box; }
  html, body {
    width: 1200px;
    height: 900px;
    overflow: hidden;
    background: var(--backdrop);
    font-family: "Lato", sans-serif;
  }
  .canvas {
    position: relative;
    width: 1200px;
    height: 900px;
  }
  .card {
    position: absolute;
    width: 500px;
    height: 300px;
    border-radius: 26px;
    box-shadow: 0 10px 28px var(--card-shadow);
    display: flex;
    flex-direction: column;
    align-items: center;
    justify-content: center;
  }
  .card--front {
    left: 90px;
    top: 150px;
    background: var(--leaf-green);
  }
  .card--back {
    left: 610px;
    top: 450px;
    background: var(--paper-white);
  }
  .brand {
    display: flex;
    align-items: center;
    gap: 12px;
  }
  .brand__mark {
    width: 26px;
    height: 26px;
  }
  .brand__name {
    font-weight: 900;
    font-size: 52px;
    letter-spacing: 0.5px;
    line-height: 1;
  }
  .card--front .brand__mark { background: var(--paper-white); }
  .card--front .brand__name { color: var(--paper-white); }
  .card--back .brand__mark { background: var(--leaf-green); }
  .card--back .brand__name { color: var(--leaf-green); }
  .card--back .brand { margin-top: 10px; }
  .contact {
    margin-top: 34px;
    display: flex;
    flex-direction: column;
    align-items: center;
    gap: 10px;
    font-size: 17px;
    color: var(--ink-grey);
  }
  .contact__row {
    display: flex;
    gap: 26px;
  }
  .contact__item {
    display: flex;
    align-items: center;
    gap: 6px;
  }
  .contact__icon {
    width: 18px;
    height: 18px;
    flex: none;
  }
  .contact__web { font-size: 18px; }
  .contact__web-highlight { color: var(--leaf-green); }
</style>
</head>
<body>
  <main class="canvas">
    <section class="card card--front" aria-label="Card front">
      <div class="brand">
        <span class="brand__mark"></span>
        <span class="brand__name">alpinleaf</span>
      </div>
    </section>

    <section class="card card--back" aria-label="Card back">
      <div class="brand">
        <span class="brand__mark"></span>
        <span class="brand__name">alpinleaf</span>
      </div>
      <div class="contact">
        <div class="contact__row">
          <span class="contact__item">
            <svg class="contact__icon" viewBox="0 0 24 24" aria-hidden="true">
              <circle cx="12" cy="12" r="11" fill="#9cc96b"/>
              <path d="M8.2 6.5c.5-.3 1-.2 1.3.3l1.1 1.9c.3.5.1 1-.3 1.3l-.7.5c.6 1.4 1.7 2.6 3.1 3.3l.6-.7c.3-.4.9-.5 1.3-.2l1.9 1.2c.5.3.6.8.3 1.3-.7 1.2-1.9 1.7-3.1 1.3-3.2-1-5.6-3.5-6.5-6.7-.3-1.1.2-2.2 1-2.8z" fill="#ffffff"/>
            </svg>
            +41 79 415 62 30
          </span>
          <span class="contact__item">
            <svg class="contact__icon" viewBox="0 0 24 24" aria-hidden="true">
              <rect x="2" y="5" width="20" height="14" rx="1.5" fill="#9cc96b"/>
              <path d="M3 6.5l9 6.5 9-6.5" fill="none" stroke="#ffffff" stroke-width="1.6"/>
            </svg>
            office@alpinleaf.net
          </span>
        </div>
        <span class="contact__web">www.<span class="contact__web-highlight">alpinleaf</span>.net</span>
      </div>
    </section>
  </main>
</body>
</html>
```